Brightway Coordination Group Business card

We wish to have a professional Business card to present to large Corporate CEO's ASAP.

Our web site helps explain our business www.brightwaycg.org

Brightway Coordination Group was established after we discovered how difficult it is to organise outsourced services while heading up a business or company.

We act as a facilitator for businesses who don't have the desire, expertise or recourses to manage their own systems and meet all their requirements.

We provide an all in one facility management solution for all types of businesses. We manage schedules, contractors and costs on behalf of businesses and their needs and wants.

Having an extensive network ensures we are able to connect businesses with the right service providers.

Target Market(s)

Company CEO

Industry/Entity Type

Business

Font styles to use
Sans Serif

Colors
33a6d7
f9fdfe
0355a3

Requirements
Must have
• professional design
Nice to have
• colours to match logo

```html
<!DOCTYPE html>
<html lang="en">
<head>
<meta charset="utf-8">
<title>Brightway Coordination Group – Business Card</title>
<link href="https://fonts.googleapis.com/css2?family=Lato:wght@400;700&display=swap" rel="stylesheet">
<style>
  :root {
    --brand-sky: #33a6d7;
    --brand-sky-deep: #1c9cc9;
    --brand-navy: #0355a3;
    --paper: #f9fdfe;
    --paper-shade: #eef1f2;
    --ink-soft: #e8f6fb;
    --backdrop: #2b2b2b;
  }
  * { box-sizing: border-box; margin: 0; padding: 0; }
  html, body {
    width: 1200px; height: 997px; overflow: hidden;
    background: var(--backdrop);
    font-family: "Lato", sans-serif;
  }
  .sheet {
    width: 1200px; height: 997px;
    display: flex; flex-direction: column; align-items: center; justify-content: center;
    gap: 60px;
  }
  .card {
    position: relative;
    width: 700px; height: 400px;
    border-radius: 22px;
    overflow: hidden;
    background: linear-gradient(180deg, #ffffff 0%, var(--paper) 60%, var(--paper-shade) 100%);
  }
  .brand {
    display: flex; align-items: center; gap: 14px;
  }
  .brand__dot {
    width: 46px; height: 46px; border-radius: 50%;
    background: var(--brand-sky);
    flex: none;
  }
  .brand__name {
    font-weight: 700;
    font-size: 26px;
    letter-spacing: 1px;
    text-transform: uppercase;
    color: var(--brand-navy);
    line-height: 1.1;
  }
  .card--front {
    display: flex; align-items: center; justify-content: center;
  }
  .card--back .brand {
    position: absolute; left: 56px; top: 62px;
  }
  .card__band {
    position: absolute; left: 0; right: 0; bottom: 0; height: 215px;
    background: linear-gradient(180deg, var(--brand-sky) 0%, var(--brand-sky-deep) 100%);
  }
  .card__stripe {
    position: absolute; left: 0; right: 0; height: 4px;
    background: var(--paper);
  }
  .card__stripe--one { top: 14px; }
  .card__stripe--two { top: 26px; }
  .card__stripe--three { top: 38px; }
  .holder {
    position: absolute; left: 56px; bottom: 48px;
    font-size: 26px; letter-spacing: 1px;
    color: var(--ink-soft); text-transform: uppercase;
  }
  .contact {
    position: absolute; right: 48px; top: 74px;
    list-style: none;
    display: flex; flex-direction: column; gap: 12px;
  }
  .contact__item {
    display: flex; align-items: center; gap: 10px;
    font-size: 17px; color: #ffffff; letter-spacing: .3px;
  }
  .contact__icon {
    width: 26px; height: 26px; flex: none;
  }
</style>
</head>
<body>
<main class="sheet">
  <section class="card card--front" aria-label="Card front">
    <div class="brand">
      <span class="brand__dot"></span>
      <span class="brand__name">Brightway Coordination Group</span>
    </div>
  </section>

  <section class="card card--back" aria-label="Card back">
    <div class="brand">
      <span class="brand__dot"></span>
      <span class="brand__name">Brightway Coordination Group</span>
    </div>
    <div class="card__band">
      <span class="card__stripe card__stripe--one"></span>
      <span class="card__stripe card__stripe--two"></span>
      <span class="card__stripe card__stripe--three"></span>
      <p class="holder">Ethan Marlow</p>
      <ul class="contact">
        <li class="contact__item">
          <svg class="contact__icon" viewBox="0 0 26 26" aria-hidden="true">
            <rect width="26" height="26" rx="3" fill="#f9fdfe"/>
            <path d="M8 7c1-1 2-1 3 0l1 2c0 1 0 1-1 2 1 2 2 3 4 4 1-1 1-1 2-1l2 1c1 1 1 2 0 3-2 2-5 1-8-2s-4-6-3-9z" fill="#33a6d7"/>
          </svg>
          0400 128 375
        </li>
        <li class="contact__item">
          <svg class="contact__icon" viewBox="0 0 26 26" aria-hidden="true">
            <rect width="26" height="26" rx="3" fill="#f9fdfe"/>
            <path d="M11 15l4-4M10 12l-2 2a3 3 0 0 0 4 4l2-2M16 14l2-2a3 3 0 0 0-4-4l-2 2" stroke="#33a6d7" stroke-width="2" fill="none" stroke-linecap="round"/>
          </svg>
          www.brightwaycg.org
        </li>
        <li class="contact__item">
          <svg class="contact__icon" viewBox="0 0 26 26" aria-hidden="true">
            <rect width="26" height="26" rx="3" fill="#f9fdfe"/>
            <rect x="5" y="8" width="16" height="11" fill="none" stroke="#33a6d7" stroke-width="1.8"/>
            <path d="M5 8l8 6 8-6" fill="none" stroke="#33a6d7" stroke-width="1.8"/>
          </svg>
          ethan@brightwaycg.org
        </li>
      </ul>
    </div>
  </section>
</main>
</body>
</html>
```